Eye Catching Business Card for Optometrist

We've recently refreshed our logo and now we need a fresh and bold look for our business cards. We provide progressive ways to improve people's vision and protect their eye health.

Use our new logo as guidance into the colors to use. As far as style goes, I love how bold and eye catching the card is for Lanternfield Studio. Feel free to use your creative judgement.

Tagline: "Clearly the best for your vision."

pertinent info to include:

Dr. Marcus Velbrin
Optometrist

7258 Dunmore Ridge Blvd #215
Brantwell, MO 64172
(555) 382-9017

marc@brantwellfamilyeyecare.example
www.brantwellfamilyeyecare.example

```html
<!DOCTYPE html>
<html lang="en">
<head>
<meta charset="utf-8">
<title>Brantwell Family Eye Care – Business Card</title>
<link rel="stylesheet" href="https://fonts.googleapis.com/css2?family=Lato:wght@400;700&display=swap">
<style>
  :root {
    --backdrop: #dfe8ef;
    --card-front: #ffffff;
    --card-back: #f5f3f3;
    --brand-red: #c8202f;
    --brand-brown: #6e5d52;
    --brand-sand: #d4bc9e;
    --text-dark: #4a3f38;
    --text-muted: #5c524b;
    --ghost: #f0dcd6;
  }
  * { box-sizing: border-box; margin: 0; padding: 0; }
  html, body { width: 1200px; height: 960px; overflow: hidden; }
  body {
    background: var(--backdrop);
    font-family: "Lato", sans-serif;
    position: relative;
  }
  .card {
    position: absolute;
    width: 648px;
    height: 367px;
    box-shadow: 0 3px 8px rgba(40, 50, 60, 0.25);
    overflow: hidden;
  }
  .card--front { left: 278px; top: 72px; background: var(--card-front); }
  .card--back  { left: 279px; top: 506px; height: 371px; background: var(--card-back); }

  .brand {
    position: absolute;
    display: flex;
    align-items: center;
    gap: 12px;
  }
  .brand__mark {
    width: 44px; height: 44px;
    background: var(--brand-red);
    flex: none;
  }
  .brand__name {
    font-weight: 700;
    color: var(--brand-red);
    text-transform: uppercase;
    line-height: 1.1;
    letter-spacing: 0.02em;
  }
  .card--front .brand { left: 43px; top: 62px; }
  .card--front .brand__name { font-size: 19px; }
  .card--back .brand { left: 330px; top: 58px; }
  .card--back .brand__name { font-size: 27px; }
  .card--back .brand__mark { width: 62px; height: 62px; }

  .person { position: absolute; left: 43px; top: 198px; }
  .person__name { font-size: 19px; font-weight: 700; color: var(--brand-red); }
  .person__title { font-size: 14px; color: var(--text-dark); margin-top: 3px; }

  .address {
    position: absolute; right: 47px; top: 159px;
    text-align: right; font-size: 14px; line-height: 19px;
    color: var(--text-dark); font-style: normal;
  }
  .contacts {
    position: absolute; right: 31px; top: 231px;
    list-style: none; font-size: 14px; line-height: 19.5px;
    color: var(--text-dark);
  }
  .contacts li { display: flex; justify-content: flex-end; align-items: center; gap: 8px; }
  .contacts svg { width: 14px; height: 14px; flex: none; }

  .swoosh { position: absolute; left: 0; bottom: 0; width: 648px; height: 60px; }

  .ghost-name {
    position: absolute; left: 14px; top: 245px;
    font-weight: 700; color: var(--ghost); text-transform: uppercase; line-height: 1.05;
  }
  .ghost-name__top { font-size: 36px; }
  .ghost-name__bottom { font-size: 55px; }
</style>
</head>
<body>

<section class="card card--front" aria-label="Business card front">
  <div class="brand">
    <span class="brand__mark"></span>
    <span class="brand__name">Brantwell Family<br>Eye Care</span>
  </div>

  <div class="person">
    <p class="person__name">Dr. Marcus Velbrin</p>
    <p class="person__title">Optometrist</p>
  </div>

  <address class="address">
    7258 Dunmore Ridge Blvd #215<br>
    Brantwell, MO 64172
  </address>

  <ul class="contacts">
    <li>(555) 382-9017
      <svg viewBox="0 0 14 14" aria-hidden="true"><rect x="3.5" y="1" width="7" height="12" rx="1.2" fill="none" stroke="#c8202f" stroke-width="1.4"/><line x1="6" y1="11" x2="8" y2="11" stroke="#c8202f" stroke-width="1"/></svg>
    </li>
    <li>marc@brantwellfamilyeyecare.example
      <svg viewBox="0 0 14 14" aria-hidden="true"><rect x="1" y="3" width="12" height="9" fill="#c8202f"/><polyline points="1,3 7,8 13,3" fill="none" stroke="#fff" stroke-width="1"/></svg>
    </li>
    <li>www.brantwellfamilyeyecare.example
      <svg viewBox="0 0 14 14" aria-hidden="true"><rect x="1" y="2" width="12" height="8" fill="none" stroke="#c8202f" stroke-width="1.4"/><rect x="5" y="11" width="4" height="1.6" fill="#c8202f"/></svg>
    </li>
  </ul>

  <svg class="swoosh" viewBox="0 0 648 60" preserveAspectRatio="none" aria-hidden="true">
    <path d="M0,60 L0,56 Q300,2 648,58 L648,60 Z" fill="var(--brand-sand)"/>
    <path d="M0,54 Q300,-4 648,56 L648,52 Q300,-12 0,50 Z" fill="var(--brand-red)"/>
    <path d="M0,55 Q300,-3 648,57" fill="none" stroke="#fff" stroke-width="1.5"/>
  </svg>
</section>

<section class="card card--back" aria-label="Business card back">
  <div class="brand">
    <span class="brand__mark"></span>
    <span class="brand__name">Brantwell Family<br>Eye Care</span>
  </div>

  <p class="ghost-name" aria-hidden="true">
    <span class="ghost-name__top">Brantwell Family</span><br>
    <span class="ghost-name__bottom">Eye Care</span>
  </p>
</section>

</body>
</html>
```